Need App for Impact Related Events

My app is to help with internal events. When you enter the prompted event code the next screen shows you everyone currently at the event. It will give you the ability to Start a conversation with someone you met at that event, or signal it is your turn to send a message. The next screen is a message thread with that person. I am looking for a design that incorporates the colors and ‘feel good’ emotion of our logo. I have pieced together a pretty good interpretation of what I’m looking for in the attached mockup by slicing and dicing designs. I also attached our logo mascot.Screens (see attached mockups)

Note 1: I do not like the picture on the screen used in screen one because it makes it seem like a dating app. I attached an alternative photo that can be used or present different ideas.

Note 2: On the login/signup screen (screen 2) I need an additional first and last name for login, you can try to fit this on one login screen or present a two step signup screen where that is presented in the second screen.

READ MOCKUP GUIDELINES UNDER Must Haves

Target Market(s)

People attending internal social impact events

Industry/Entity Type

Charity

Font styles to use
Sans Serif

Colors
86cfc6

Requirements
Must have
• Follow the screen mockups attached to project
• PLEASE READ
• I have provided a relatively close design of what I’m looking for in the mockups. Some screens need to be followed more closely to my design mockup than other. I have listed a guide below how how closely you should follow my mockup design exactly. Overall I would like to see some ideas of incorporating a few accent colors so it doesn’t appear SO Blue. I also attached some app inspiration designs I found from around the web
• Screen Mockup Guideline Follow %
• Screen 1: 65% - mostly on target, would like to see ways to make it not SO Blue and possibly creative places to add some explainer text describing the app
• Screen 2: 50% - general design idea is here, but more open
• Screen 3: 35% - a lot more room for design influence
• Screen 4: 70% - mostly on target, a little room for design influence/color scheme ideas
• Screen 5-6: 25% - a lot of room for design change/ideas/influence
• Screen 7-8: 80% - already very close to what I need, maybe open to slight sizing and color scheme ideas
• Screen 9: 15% - the most open for influence, only the general functionality of the screen is communicated here
Nice to have
• Please Read Mockup Guideline above. In large part I am looking for something to use some nice accent colors so it is not overwhelmingly blue and bring the whole design into a seamless style.
Should not have

```html
<!DOCTYPE html>
<html lang="en">
<head>
<meta charset="utf-8">
<title>Manage Events</title>
<link rel="stylesheet" href="https://fonts.googleapis.com/css2?family=Lato:wght@400;700;900&family=Roboto:wght@400&display=swap">
<style>
  :root {
    --bg: #ffffff;
    --ink: #23232f;
    --field-text: #3e4252;
    --placeholder: #8a8d97;
    --field-border: #e4e4e8;
    --brand-teal: #86cfc6;
    --teal-deep: #3fa99c;
    --accent: #8b4ff0;
    --danger: #ff2222;
    --save-start: #8c52ea;
    --save-end: #86cfc6;
    --kb-bar: #eceff1;
    --kb-bg: #fafafa;
    --kb-key: #2b2b2b;
    --kb-hint: #5f6368;
    --kb-divider: #c4c7cb;
    --kb-space: #d9d9d9;
    --kb-enter: #4285f4;
  }
  * { box-sizing: border-box; margin: 0; padding: 0; }
  html, body { width: 675px; height: 1200px; overflow: hidden; background: var(--bg); }
  .screen { position: relative; width: 675px; height: 1200px; overflow: hidden; font-family: "Lato", sans-serif; }

  .back { position: absolute; left: 38px; top: 52px; width: 26px; height: 30px; }
  .title { position: absolute; left: 58px; top: 158px; font-size: 60px; font-weight: 900; color: var(--ink); letter-spacing: 0.5px; line-height: 1.2; }

  .field { position: absolute; left: 56px; width: 563px; height: 75px; border: 2px solid var(--field-border); border-radius: 8px; display: flex; align-items: center; justify-content: space-between; padding: 0 26px; }
  .field-name { top: 308px; font-size: 28px; font-weight: 700; color: var(--field-text); border-color: var(--brand-teal); }
  .field-category { top: 401px; font-size: 25px; color: var(--placeholder); }

  .btn { position: absolute; top: 622px; height: 76px; border-radius: 7px; display: flex; align-items: center; justify-content: center; color: #fff; font-weight: 900; letter-spacing: 1.5px; box-shadow: 0 4px 10px rgba(0,0,0,0.12); }
  .btn-delete { left: 30px; width: 178px; background: var(--danger); font-size: 24px; }
  .btn-save { left: 319px; width: 300px; background: linear-gradient(90deg, var(--save-start), var(--save-end)); font-size: 22px; }

  .keyboard { position: absolute; left: 0; top: 735px; width: 675px; height: 465px; background: var(--kb-bg); font-family: "Roboto", sans-serif; color: var(--kb-key); }
  .suggestions { position: relative; height: 75px; background: var(--kb-bar); font-size: 28px; color: #3c4043; }
  .suggestions span { position: absolute; top: 22px; transform: translateX(-50%); }
  .suggestions .divider { position: absolute; top: 20px; width: 2px; height: 36px; background: var(--kb-divider); }
  .suggestions .mic { position: absolute; left: 631px; top: 20px; }

  .key { position: absolute; width: 40px; text-align: center; font-size: 36px; transform: translateX(-50%); }
  .key sup { position: absolute; top: -24px; right: -4px; font-size: 18px; color: var(--kb-hint); }
  .row1 .key { top: 110px; }
  .row2 .key { top: 205px; }
  .row3 .key { top: 300px; }
  .symbols { position: absolute; left: 22px; top: 392px; font-size: 26px; }
  .space { position: absolute; left: 253px; top: 386px; width: 235px; height: 42px; background: var(--kb-space); border-radius: 4px; }
  .enter { position: absolute; left: 592px; top: 379px; width: 58px; height: 58px; border-radius: 50%; background: var(--kb-enter); display: flex; align-items: center; justify-content: center; }
</style>
</head>
<body>
<main class="screen">
  <svg class="back" viewBox="0 0 26 30" aria-label="Back"><path d="M18 3 L6 15 L18 27" fill="none" stroke="var(--teal-deep)" stroke-width="3" stroke-linecap="round" stroke-linejoin="round"/></svg>

  <h1 class="title">Manage Events</h1>

  <div class="field field-name">
    <span>Nora's Birthday</span>
    <svg width="30" height="30" viewBox="0 0 30 30" aria-label="Edit"><path d="M5 25 L7 18 L20 5 L25 10 L12 23 Z M17 8 L22 13 M7 18 L12 23" fill="none" stroke="var(--teal-deep)" stroke-width="2.4" stroke-linejoin="round"/></svg>
  </div>

  <div class="field field-category">
    <span>Category</span>
    <svg width="36" height="22" viewBox="0 0 36 22" aria-label="Open"><path d="M4 5 L18 17 L32 5" fill="none" stroke="var(--teal-deep)" stroke-width="3" stroke-linecap="round" stroke-linejoin="round"/></svg>
  </div>

  <div class="btn btn-delete">DELETE</div>
  <div class="btn btn-save">SAVE EVENT</div>

  <section class="keyboard">
    <div class="suggestions">
      <span style="left:148px">Hi</span>
      <i class="divider" style="left:237px"></i>
      <span style="left:334px">Hello</span>
      <i class="divider" style="left:434px"></i>
      <span style="left:521px">Howdy</span>
      <svg class="mic" width="24" height="36" viewBox="0 0 24 36" aria-label="Voice"><rect x="6" y="2" width="12" height="20" rx="6" fill="#5f6368"/><path d="M2 16 A10 10 0 0 0 22 16 M12 26 V33" fill="none" stroke="#5f6368" stroke-width="2.5"/></svg>
    </div>

    <div class="row1">
      <div class="key" style="left:34px">q<sup>1</sup></div>
      <div class="key" style="left:101px">w<sup>2</sup></div>
      <div class="key" style="left:169px">e<sup>3</sup></div>
      <div class="key" style="left:236px">r<sup>4</sup></div>
      <div class="key" style="left:304px">t<sup>5</sup></div>
      <div class="key" style="left:371px">y<sup>6</sup></div>
      <div class="key" style="left:439px">u<sup>7</sup></div>
      <div class="key" style="left:506px">i<sup>8</sup></div>
      <div class="key" style="left:574px">o<sup>9</sup></div>
      <div class="key" style="left:638px">p<sup>0</sup></div>
    </div>
    <div class="row2">
      <div class="key" style="left:68px">a</div>
      <div class="key" style="left:135px">s</div>
      <div class="key" style="left:203px">d</div>
      <div class="key" style="left:270px">f</div>
      <div class="key" style="left:338px">g</div>
      <div class="key" style="left:405px">h</div>
      <div class="key" style="left:473px">j</div>
      <div class="key" style="left:540px">k</div>
      <div class="key" style="left:608px">l</div>
    </div>
    <div class="row3">
      <svg style="position:absolute;left:36px;top:300px" width="34" height="40" viewBox="0 0 34 40" aria-label="Shift"><path d="M17 3 L31 19 H23 V30 H11 V19 H3 Z" fill="#3c4043"/><rect x="9" y="35" width="16" height="3" fill="#3c4043"/></svg>
      <div class="key" style="left:135px">z</div>
      <div class="key" style="left:203px">x</div>
      <div class="key" style="left:270px">c</div>
      <div class="key" style="left:338px">v</div>
      <div class="key" style="left:405px">b</div>
      <div class="key" style="left:473px">n</div>
      <div class="key" style="left:540px">m</div>
      <svg style="position:absolute;left:600px;top:306px" width="42" height="28" viewBox="0 0 42 28" aria-label="Backspace"><path d="M12 2 H40 V26 H12 L1 14 Z" fill="#3c4043"/><path d="M20 8 L32 20 M32 8 L20 20" stroke="#fafafa" stroke-width="3"/></svg>
    </div>
    <div class="row4">
      <div class="symbols">?123</div>
      <div class="key" style="left:135px;top:380px">,</div>
      <svg style="position:absolute;left:187px;top:390px" width="32" height="32" viewBox="0 0 32 32" aria-label="Emoji"><circle cx="16" cy="16" r="13" fill="none" stroke="#3c4043" stroke-width="2.5"/></svg>
      <div class="space"></div>
      <div class="key" style="left:538px;top:380px">.</div>
      <div class="enter"><svg width="30" height="24" viewBox="0 0 30 24" aria-label="Enter"><path d="M25 3 V13 H6 M12 7 L5 13 L12 19" fill="none" stroke="#fff" stroke-width="3" stroke-linejoin="round"/></svg></div>
    </div>
  </section>
</main>
</body>
</html>
```